High profile consulting company needs a Business Card Design

I need a business card design for a coaching /consulting company. We specialize in changing behaviors. Our services include therapy, workshops, life coaching, etc.

Check out our website to get a feel for our personality. www.oakbridgeadvisory.com

The new logo will be attached to the website soon, I have attached the new logo for your use on the business card.
Updates

I forgot to provide you with the company email under the "must have" section for the business card.  The website is:

 www.oakbridgeadvisory.com

I understand there's some trouble with the logo I uploaded.  I will try that again.  Thank you for your efforts.

Dana

Thank you for some of your questions.  I prefer a one sided business card, and tend to like the white backgrounds.

I also made 2 small changes to the content.  

add MFT after the name:  Dana Holloway, MFT

and the tag line needed more clarity once I saw it.  Please change it to:  Improving performance by strengthening relationships and changing behaviors.

Thank you,
Dana

Industry/Entity Type

Business

Requirements
Must have
• logo
Phone number: 415-207-5146
email: Dana@oakbridgeadvisory.com
Dana Holloway, MFT
President
Nice to have
• Improving performance by strengthening relationships and changing behaviors.

```html
<!DOCTYPE html>
<html lang="en">
<head>
<meta charset="utf-8">
<title>Oakbridge Advisory – Business Card</title>
<link rel="stylesheet" href="https://fonts.googleapis.com/css2?family=Arimo:wght@400;700&display=swap">
<style>
  :root {
    --brand-green: #127a56;
    --brand-green-light: #1f9a6d;
    --brand-gray: #6d6e70;
    --ink: #231f20;
    --card-white: #ffffff;
    --backdrop: #e6e7e8;
  }
  * { box-sizing: border-box; margin: 0; padding: 0; }
  html, body { width: 1200px; height: 944px; overflow: hidden; }
  body { background: var(--backdrop); font-family: "Arimo", Arial, sans-serif; color: var(--ink); }
  .canvas {
    position: relative; width: 1200px; height: 944px;
    display: flex; flex-direction: column; align-items: center; justify-content: center; gap: 44px;
  }
  .card {
    position: relative; width: 700px; height: 400px;
    background: var(--card-white); border-radius: 26px; overflow: hidden;
    box-shadow: 0 8px 24px rgba(0,0,0,0.18);
  }
  .brand { position: absolute; display: flex; align-items: center; gap: 18px; }
  .brand-dot {
    width: 92px; height: 92px; border-radius: 50%;
    background: var(--brand-gray); flex: none;
  }
  .brand-name {
    font-weight: 700; font-size: 46px; letter-spacing: 1px;
    color: var(--brand-green); text-transform: uppercase; line-height: 1.05;
  }
  .card-front .brand { left: 70px; top: 92px; }
  .tagline {
    position: absolute; left: 0; right: 0; top: 258px;
    text-align: center; font-size: 17px; line-height: 1.3; color: var(--ink);
  }
  .card-back .brand { left: 120px; top: 48px; }
  .holder { position: absolute; left: 40px; top: 196px; }
  .holder-name { font-size: 26px; color: var(--ink); }
  .holder-title { font-size: 17px; color: var(--brand-green); margin-top: 4px; }
  .contact { position: absolute; left: 372px; top: 196px; list-style: none; }
  .contact li { display: flex; align-items: center; gap: 12px; font-size: 17px; line-height: 26px; }
  .contact svg { width: 16px; height: 16px; flex: none; }
  .footer-band {
    position: absolute; left: 0; right: 0; bottom: 0; height: 96px;
    background: linear-gradient(180deg, var(--ink) 0%, var(--ink) 30%, var(--brand-green) 62%, var(--brand-green-light) 100%);
  }
</style>
</head>
<body>
<main class="canvas">
  <section class="card card-front" aria-label="Card front">
    <div class="brand">
      <span class="brand-dot"></span>
      <span class="brand-name">Oakbridge<br>Advisory</span>
    </div>
    <p class="tagline">Improving performance by<br>strengthening relationships and changing behaviors.</p>
  </section>

  <section class="card card-back" aria-label="Card back">
    <div class="brand">
      <span class="brand-dot"></span>
      <span class="brand-name">Oakbridge<br>Advisory</span>
    </div>

    <div class="holder">
      <p class="holder-name">Dana Holloway</p>
      <p class="holder-title">MFT, President</p>
    </div>

    <ul class="contact">
      <li>
        <svg viewBox="0 0 16 16" aria-hidden="true"><circle cx="8" cy="8" r="8" fill="var(--brand-green)"/><path d="M5 4 h2 l1 2 -1 1 a5 5 0 0 0 2 2 l1 -1 2 1 v2 a1 1 0 0 1 -1 1 A7 7 0 0 1 4 5 a1 1 0 0 1 1 -1z" fill="#fff"/></svg>
        <span>415-207-5146</span>
      </li>
      <li>
        <svg viewBox="0 0 16 16" aria-hidden="true"><circle cx="8" cy="8" r="8" fill="var(--brand-green)"/><rect x="4" y="5" width="8" height="6" fill="#fff"/><path d="M4 5 L8 8.5 L12 5" stroke="var(--brand-green)" fill="none"/></svg>
        <span>Dana@oakbridgeadvisory.com</span>
      </li>
      <li>
        <svg viewBox="0 0 16 16" aria-hidden="true"><circle cx="8" cy="8" r="8" fill="var(--brand-green)"/><circle cx="8" cy="8" r="4" fill="none" stroke="#fff"/><path d="M4 8 h8 M8 4 v8" stroke="#fff"/></svg>
        <span>www.oakbridgeadvisory.com</span>
      </li>
    </ul>

    <div class="footer-band" role="img" aria-label="Decorative black and green wave bands along the bottom edge"></div>
  </section>
</main>
</body>
</html>
```